Redesign This Psychology Website

We would like a slight redesign of this successful psychology (relationship counselling) website:

www.TheKelvaleClinic.com.au

We are updating the website, and we'd like a slight refresh of the design and style.

Please keep to very similar colours, and use the same logo. We're looking for around 10 page templates, however the main one is the home page.

Keep in mind, this website already converts quite well, so we want a new, fresh design in keeping with this one. Please don't bother designing something too extremely different.

thanks :)

Target Market(s)

couples who are looking for relationship counselling. Men and women, 25 - 70, across Australia

Industry/Entity Type

Psychology

Number of Pages Required

5+ page

Font styles to use
Sans Serif

Colors
87cfc6
b7a5cd
ec1f27
ffffff
cee9f5

Requirements
Must have
• a similar look to the current design, just looking for a slight refresh.
• Search bar
• Areas for lots of photos
• same logo
• lots of content areas
Nice to have
• great content areas, where we can display a lot of content and our areas.
Should not have
• no colors like orange, etc.
• should not have a totally different feel.

```html
<!DOCTYPE html>
<html lang="en">
<head>
<meta charset="utf-8">
<title>FAQ – Kelvale Clinic</title>
<link href="https://fonts.googleapis.com/css2?family=Nunito+Sans:wght@400;600;700&family=Open+Sans:wght@400;600&display=swap" rel="stylesheet">
<style>
:root{
  --teal:#87cfc6;
  --teal-dark:#6cc0b6;
  --teal-deep:#0d7b8a;
  --teal-text:#138a99;
  --purple:#b7a5cd;
  --red:#ec1f27;
  --white:#ffffff;
  --sky:#cee9f5;
  --ink:#333a40;
  --grey:#6b7278;
  --line:#d9dcde;
  --bar:#f1f1f1;
}
*{box-sizing:border-box;margin:0;padding:0}
html,body{width:1200px;height:2341px;overflow:hidden}
body{position:relative;background:var(--white);font-family:"Open Sans",Arial,sans-serif;color:var(--ink)}
a{color:inherit;text-decoration:none}

.topbar{position:absolute;left:0;top:0;width:1200px;height:37px;background:var(--bar);border-bottom:1px solid #e2e2e2}
.topbar .promo{position:absolute;left:133px;top:9px;font:400 14px "Nunito Sans",sans-serif;color:#666}
.toplinks{position:absolute;right:146px;top:0;display:flex;height:37px}
.toplinks a{font:400 14px "Nunito Sans",sans-serif;color:#777;padding:9px 12px 0;border-left:1px solid #d8d8d8}
.toplinks a:first-child{border-left:none}

.header{position:absolute;top:37px;left:0;width:1200px;height:124px;background:var(--white)}
.brand{position:absolute;display:flex;align-items:center;gap:12px}
.brand .dot{width:52px;height:52px;border-radius:50%;background:var(--teal-deep);flex:none}
.brand .name{font:600 34px/1 "Nunito Sans",sans-serif;color:var(--teal-deep)}
.header .brand{left:117px;top:36px}
.search{position:absolute;left:457px;top:47px;width:356px;height:38px;border:1px solid #cfd3d6;border-radius:2px;display:flex;align-items:center;padding-left:10px;gap:8px;font-size:13px;color:#999}
.callus{position:absolute;right:103px;top:38px;text-align:right}
.callus .label{font:400 17px "Nunito Sans",sans-serif;color:var(--teal);padding-right:46px}
.callus .phone{display:flex;align-items:center;gap:6px;font:600 27px "Nunito Sans",sans-serif;color:var(--teal-deep)}

.mainnav{position:absolute;top:161px;left:0;width:1200px;height:67px;background:linear-gradient(var(--teal),#a6dcd5 60%,var(--teal-dark))}
.mainnav ul{list-style:none;display:flex;position:absolute;left:112px;top:0;height:67px}
.mainnav li{display:flex;align-items:center;justify-content:center;padding:0 8px;border-left:1px solid rgba(255,255,255,.55);font:600 16px/1.05 "Nunito Sans",sans-serif;color:var(--white);text-transform:uppercase}
.mainnav li:first-child{border-left:none}
.mainnav li.left{justify-content:flex-start;padding-left:10px}

.hero{position:absolute;top:228px;left:0;width:1200px;height:324px;background:linear-gradient(110deg,#6e5d52 0%,#b9a595 35%,#d8cbbd 60%,#8d7c70 100%)}
.hero h1{position:absolute;left:128px;top:170px;font:600 38px "Nunito Sans",sans-serif;color:var(--white)}

.faq-title{position:absolute;left:136px;top:612px;font:400 29px "Nunito Sans",sans-serif;color:#2d3439}
.faq{position:absolute;left:131px;top:683px;width:606px}
.faq-item{height:46px;margin-bottom:1px;background:var(--teal);display:flex;align-items:center;justify-content:space-between;padding:0 18px 0 32px;font:400 15px "Open Sans",sans-serif;color:var(--white)}
.faq-item.open{background:var(--teal-deep);height:44px;margin-bottom:0;padding-left:24px;font-size:16px}
.faq-body{height:401px;border:1px solid var(--line);border-top:none;padding:18px 24px;font-size:12.5px;line-height:23px;color:var(--grey);margin-bottom:1px}
.faq-body p{margin-bottom:8px}
.faq-body .lead{color:#4b5157;margin-bottom:0}

.finder{position:absolute;left:766px;top:599px;width:301px;height:364px;background:var(--purple);padding:26px 26px 0;color:var(--white)}
.finder h2{text-align:center;font:600 23px/1.3 "Nunito Sans",sans-serif}
.finder h2 span{display:inline-flex;align-items:center;gap:10px}
.finder h2 span:before,.finder h2 span:after{content:"";width:30px;height:1px;background:rgba(255,255,255,.8)}
.finder label{display:block;font-size:13px;margin:10px 0 4px}
.finder .field{height:33px;background:var(--white);border-radius:2px;display:flex;align-items:center;justify-content:space-between;padding:0 12px;font-size:11px;color:#888}
.finder .btn{margin-top:16px;height:38px;background:linear-gradient(#f2464c,var(--red));display:flex;align-items:center;justify-content:center;font:600 17px "Nunito Sans",sans-serif;text-transform:uppercase}

.post{position:absolute;left:774px;width:301px;height:114px;border:1px solid var(--line);display:flex;background:var(--white)}
.post .thumb{width:152px;height:112px;flex:none}
.post .text{padding:14px 10px 0 14px;font-size:13px;line-height:17px;color:#333}
.post .more{display:block;color:var(--teal);font-size:11px;margin-top:6px}

.footer{position:absolute;top:1969px;left:0;width:1200px;height:297px;background:linear-gradient(#ececec,#fff 40px)}
.footer .brand{left:137px;top:86px}
.footer .brand .dot{width:48px;height:48px}
.footer .brand .name{font-size:32px}
.fcol{position:absolute;top:64px}
.fcol h3{font:600 17px "Nunito Sans",sans-serif;color:var(--teal-deep);text-transform:uppercase;margin-bottom:8px}
.fcol li{list-style:none;font-size:13px;line-height:27px;color:#555}
.social{display:flex;gap:8px;margin-top:10px}
.social span{width:32px;height:32px;border-radius:50%;background:var(--teal-deep)}
.copy{position:absolute;top:2266px;left:0;width:1200px;height:75px;background:#efefef;text-align:center;padding-top:23px;font-size:12px;color:#666}
</style>
</head>
<body>

<div class="topbar">
  <a class="promo" href="#">Join Our Assoicate Program →</a>
  <nav class="toplinks"><a href="#">Home</a><a href="#">Cart</a><a href="#">Blog</a><a href="#">Resources</a><a href="#">Contact</a></nav>
</div>

<header class="header">
  <div class="brand"><span class="dot"></span><div class="name">Kelvale Clinic</div></div>
  <div class="search">
    <svg width="16" height="16" viewBox="0 0 16 16"><circle cx="6.5" cy="6.5" r="5" fill="none" stroke="#aaa" stroke-width="1.5"/><line x1="10.2" y1="10.2" x2="14.5" y2="14.5" stroke="#aaa" stroke-width="1.5"/></svg>
    Search here
  </div>
  <div class="callus">
    <div class="label">Call Us Now</div>
    <div class="phone"><svg width="22" height="22" viewBox="0 0 24 24"><path d="M6.6 10.8a15 15 0 0 0 6.6 6.6l2.2-2.2a1 1 0 0 1 1-.25 11.4 11.4 0 0 0 3.6.6 1 1 0 0 1 1 1V20a1 1 0 0 1-1 1A17 17 0 0 1 3 4a1 1 0 0 1 1-1h3.5a1 1 0 0 1 1 1c0 1.25.2 2.45.6 3.6a1 1 0 0 1-.25 1z" fill="none" stroke="#ec1f27" stroke-width="1.6"/></svg>1300 555 019</div>
  </div>
</header>

<nav class="mainnav"><ul>
  <li class="left" style="width:139px">Counselling<br>Types</li>
  <li class="left" style="width:268px">Relationship Counselling<br>Locations</li>
  <li class="left" style="width:133px">Sex Therapy<br>Locations</li>
  <li style="width:111px">About Us</li>
  <li style="width:104px">Quizzes</li>
  <li style="width:77px">FAQ's</li>
  <li style="width:126px">Contact</li>
</ul></nav>

<section class="hero" role="img" aria-label="Photo of a couple relaxing on the floor with a laptop">
  <h1>FAQ</h1>
</section>

<h2 class="faq-title">FAQs about our Relationship Counselling</h2>

<div class="faq">
  <div class="faq-item open">What are the fees involved, and are there any rebates?
    <svg width="16" height="10" viewBox="0 0 16 10"><polyline points="2,8 8,2 14,8" fill="none" stroke="#fff" stroke-width="2"/></svg></div>
  <div class="faq-body">
    <p class="lead">Couples Counselling and Marriage counselling sessions are 50 mins</p>
    <p class="lead" style="margin-bottom:14px">Cost: $160 &nbsp;($175 for after hours sessions or for all sessions in CBD locations)</p>
    <p>Private health rebates should apply if you have ‘psychology’ as an extra, but we recommend that you call your fund and check your level of cover if this is of concern to you. &nbsp;Unfortunately funds don’t give us these details.</p>
    <p>Medicare rebates may also apply if you are suffering anxiety, depression etc, and you are successful in applying for a Mental Health Care Plan with your doctor. &nbsp;These plans are not provided for relationship counselling as such, but you may be able to use them for appointments when you are in attendance on your own. &nbsp;It is quite common to attend some sessions on your own whilst undergoing relationship counselling. &nbsp;You may be able to use them with your partner in attendance for some appointments, but this would be up to each individual psychologist to determine once they have seen you for the first time and sighted your plan. Please contact your doctor or GP to determine your eligibility for a Mental Health Care Plan. The Medicare rebate is $84.80.</p>
  </div>
  <div class="faq-item">What happens in a marriage/relationship counselling session?<svg width="16" height="10" viewBox="0 0 16 10"><polyline points="2,2 8,8 14,2" fill="none" stroke="#fff" stroke-width="2"/></svg></div>
  <div class="faq-item">How helpful will it be?<svg width="16" height="10" viewBox="0 0 16 10"><polyline points="2,2 8,8 14,2" fill="none" stroke="#fff" stroke-width="2"/></svg></div>
  <div class="faq-item">Are we too late for relationship counselling?<svg width="16" height="10" viewBox="0 0 16 10"><polyline points="2,2 8,8 14,2" fill="none" stroke="#fff" stroke-width="2"/></svg></div>
  <div class="faq-item">Can we hope for any real lasting changes?<svg width="16" height="10" viewBox="0 0 16 10"><polyline points="2,2 8,8 14,2" fill="none" stroke="#fff" stroke-width="2"/></svg></div>
  <div class="faq-item">Do you take sides?<svg width="16" height="10" viewBox="0 0 16 10"><polyline points="2,2 8,8 14,2" fill="none" stroke="#fff" stroke-width="2"/></svg></div>
  <div class="faq-item">Do you support relationships or individuals first?<svg width="16" height="10" viewBox="0 0 16 10"><polyline points="2,2 8,8 14,2" fill="none" stroke="#fff" stroke-width="2"/></svg></div>
  <div class="faq-item">(For men) Will the girls gang up on me?<svg width="16" height="10" viewBox="0 0 16 10"><polyline points="2,2 8,8 14,2" fill="none" stroke="#fff" stroke-width="2"/></svg></div>
  <div class="faq-item">Should we first come to sessions together or on our own?<svg width="16" height="10" viewBox="0 0 16 10"><polyline points="2,2 8,8 14,2" fill="none" stroke="#fff" stroke-width="2"/></svg></div>
  <div class="faq-item">What do I do if my partner doesn’t want to come?<svg width="16" height="10" viewBox="0 0 16 10"><polyline points="2,2 8,8 14,2" fill="none" stroke="#fff" stroke-width="2"/></svg></div>
  <div class="faq-item">Can I come on my own without my partner knowing?<svg width="16" height="10" viewBox="0 0 16 10"><polyline points="2,2 8,8 14,2" fill="none" stroke="#fff" stroke-width="2"/></svg></div>
  <div class="faq-item">How do I prepare for the first session?<svg width="16" height="10" viewBox="0 0 16 10"><polyline points="2,2 8,8 14,2" fill="none" stroke="#fff" stroke-width="2"/></svg></div>
  <div class="faq-item">What if it doesn’t work?<svg width="16" height="10" viewBox="0 0 16 10"><polyline points="2,2 8,8 14,2" fill="none" stroke="#fff" stroke-width="2"/></svg></div>
  <div class="faq-item">What if I cancel?<svg width="16" height="10" viewBox="0 0 16 10"><polyline points="2,2 8,8 14,2" fill="none" stroke="#fff" stroke-width="2"/></svg></div>
  <div class="faq-item">Would online video counselling be suitable for us or me?<svg width="16" height="10" viewBox="0 0 16 10"><polyline points="2,2 8,8 14,2" fill="none" stroke="#fff" stroke-width="2"/></svg></div>
</div>

<aside class="finder">
  <h2>Find Our Psychologist<br><span>Near You</span></h2>
  <label>Type of Counselling</label>
  <div class="field">Select<svg width="12" height="8" viewBox="0 0 12 8"><polyline points="1,1 6,6 11,1" fill="none" stroke="#888" stroke-width="1.5"/></svg></div>
  <label>Location</label>
  <div class="field"></div>
  <label>Postcode</label>
  <div class="field"></div>
  <div class="btn">Search</div>
</aside>

<article class="post" style="top:993px"><div class="thumb" role="img" aria-label="Photo of two hands reaching across a table" style="background:linear-gradient(135deg,#e9e4dc,#b89a7c)"></div><div class="text">What can I do if I’m living with a Narcissist?<a class="more" href="#">Read More</a></div></article>
<article class="post" style="top:1120px"><div class="thumb" role="img" aria-label="Photo of a tense couple arguing" style="background:linear-gradient(135deg,#3a2f2c,#a07d6c)"></div><div class="text">Are You Living With a Steamroller?<a class="more" href="#">Read More</a></div></article>
<article class="post" style="top:1245px"><div class="thumb" role="img" aria-label="Photo of a couple sitting apart on a bed" style="background:linear-gradient(135deg,#d9d6d2,#6e6460)"></div><div class="text">Did Your Relationship Start on Rocky Ground?<a class="more" href="#">Read More</a></div></article>
<article class="post" style="top:1389px"><div class="thumb" role="img" aria-label="Photo of an upset couple in bed" style="background:linear-gradient(135deg,#d8c1a8,#8a6a55)"></div><div class="text">Why am I with a Narcissist?<a class="more" href="#">Read More</a></div></article>
<article class="post" style="top:1517px"><div class="thumb" role="img" aria-label="Photo of a couple having a serious talk" style="background:linear-gradient(135deg,#ece8e4,#8a7c74)"></div><div class="text">Letter for a Partner Doubtful About Relationship Counselling<a class="more" href="#">Read More</a></div></article>
<article class="post" style="top:1645px"><div class="thumb" role="img" aria-label="Photo of two arms arm-wrestling" style="background:linear-gradient(135deg,#e6e1c4,#c88a6a)"></div><div class="text">What Are You Like In a Relationship?<a class="more" href="#">Read More</a></div></article>
<article class="post" style="top:1773px"><div class="thumb" role="img" aria-label="Photo of a couple facing each other" style="background:linear-gradient(135deg,#2e2622,#9c7a62)"></div><div class="text">How Do I Know If I’m With a Narcissist?<a class="more" href="#">Read More</a></div></article>

<footer class="footer">
  <div class="brand"><span class="dot"></span><div class="name">Kelvale Clinic</div></div>
  <div class="fcol" style="left:459px"><h3>Quick Links</h3><ul><li>Home</li><li>About Us</li><li>Our Blogs</li><li>Shop Cart</li><li>Contact Us</li></ul></div>
  <div class="fcol" style="left:626px"><h3>Resources</h3><ul><li>Counselling Type</li><li>Sex Therapy</li><li>Quizzes</li><li>FAQ</li><li>Relationship Counselling</li></ul></div>
  <div class="fcol" style="left:830px"><h3>Contact Us</h3><ul><li>42 Harbour Lane Suite 8</li><li>1300 555 019</li><li>Email: info@kelvaleclinic.com</li></ul>
    <div class="social"><span></span><span></span><span></span><span></span></div></div>
</footer>
<div class="copy">© 2017 Company Name &nbsp;All right reserved</div>

</body>
</html>
```